Card design for orthopaedic surgeons working as The Brightwater Joint Centre

Business cards, letterhead

Colors

Designer to choose colors to be used in the design.

Requirements
Must have
• Late addition.
• Cards letterhead must have logos of
• Crestmoor Lindell College of Surgeons
• Varenwood Bone Health Association
Nice to have
• Back of card to have space for appointment time to be added by hand and some blank space for writing incidental other notes.

```html
<!DOCTYPE html>
<html lang="en">
<head>
<meta charset="utf-8">
<title>The Brightwater Joint Centre – Stationery</title>
<link rel="stylesheet" href="https://fonts.googleapis.com/css2?family=Questrial&family=PT+Sans:ital@0;1&display=swap">
<style>
  :root {
    --navy: #05324d;
    --sky: #2aa9f2;
    --ink: #4a4a4a;
    --paper: #ffffff;
    --backdrop: #dcdcdc;
    --badge: #e4edf3;
  }
  * { box-sizing: border-box; margin: 0; padding: 0; }
  html, body { width: 1200px; height: 877px; overflow: hidden; }
  body { background: var(--backdrop); font-family: "Questrial", sans-serif; color: var(--ink); position: relative; }

  .card {
    position: absolute; left: 118px; width: 368px; height: 210px;
    background: var(--paper); border-radius: 12px; overflow: hidden;
    box-shadow: 0 1px 3px rgba(0,0,0,.18);
  }
  .card-front { top: 271px; }
  .card-back { top: 530px; font-family: "PT Sans", sans-serif; }
  .wave { position: absolute; left: 0; top: 0; display: block; }

  .holder { position: absolute; right: 24px; top: 22px; text-align: right; }
  .holder-name { color: var(--sky); font-size: 13px; letter-spacing: .3px; line-height: 15px; }
  .holder-role { color: #fff; font-size: 11px; line-height: 14px; }

  .brand-name { position: absolute; color: var(--sky); white-space: nowrap; }
  .card-front .brand-name { left: 22px; top: 105px; font-size: 12.5px; }

  .affiliations { position: absolute; display: flex; gap: 8px; list-style: none; }
  .affiliations li { border-radius: 50%; background: var(--badge); border: 1px solid #c9d7e1; }
  .card-front .affiliations { right: 24px; top: 100px; }
  .card-front .affiliations li { width: 24px; height: 24px; }

  .contact-list { position: absolute; list-style: none; font-size: 9px; line-height: 10.5px; color: #666; }
  .card-front .contact-list { left: 22px; top: 147px; }
  .contact-list li { display: flex; align-items: center; gap: 4px; }
  .contact-list svg { width: 7px; height: 7px; fill: var(--navy); flex: none; }
  .card-address { position: absolute; left: 236px; top: 155px; font-size: 9px; line-height: 10.5px; color: #666; }
  .card-address .web { margin-top: 7px; }

  .appt-title { position: absolute; top: 28px; width: 100%; text-align: center; color: var(--sky); font-size: 15px; font-weight: 400; }
  .appt-row { position: absolute; left: 22px; right: 22px; color: var(--sky); font-size: 11px; display: flex; align-items: baseline; white-space: nowrap; }
  .dots { flex: 1; border-bottom: 1px dotted #888; margin: 0 2px; height: 9px; }
  .appt-name { top: 68px; }
  .appt-when { top: 102px; }
  .appt-when .ampm { font-size: 8px; margin-left: 3px; }
  .day-list { position: absolute; top: 139px; left: 24px; right: 24px; display: flex; justify-content: space-between; list-style: none; color: var(--sky); font-size: 10px; }
  .day-list li { display: flex; align-items: center; gap: 5px; }
  .day-list li::after { content: ""; width: 9px; height: 8px; border: 1.3px solid var(--navy); }
  .appt-note { position: absolute; top: 175px; width: 100%; text-align: center; font-style: italic; font-size: 7.6px; line-height: 10.5px; color: #555; }

  .letterhead {
    position: absolute; left: 557px; top: 69px; width: 527px; height: 742px;
    background: var(--paper); box-shadow: 0 1px 3px rgba(0,0,0,.15);
  }
  .letterhead .brand-name { left: 46px; top: 94px; font-size: 12.5px; }
  .letter-contact { position: absolute; right: 25px; top: 22px; text-align: right; color: #fff; font-size: 7.6px; line-height: 10px; list-style: none; letter-spacing: .2px; }
  .letter-contact li { display: flex; justify-content: flex-end; align-items: center; gap: 4px; }
  .letter-contact svg { width: 6.5px; height: 6.5px; fill: var(--sky); }
  .letter-contact .gap { margin-bottom: 3px; }
  .letter-body { position: absolute; left: 46px; top: 205px; width: 438px; font-size: 7.2px; line-height: 11.4px; color: #555; }
  .salutation { font-size: 13px; color: #555; margin-bottom: 20px; line-height: 16px; }
  .letter-body p { margin-bottom: 11.4px; }
  .closing { margin-top: 20px; }
  .signature-space { width: 62px; height: 24px; margin-top: 10px; background: #f2f4f6; }

  .letter-footer { position: absolute; left: 46px; right: 46px; bottom: 30px; border-top: 1px solid #d5dee5; padding-top: 12px; }
  .letter-footer .affiliations { position: static; justify-content: flex-end; gap: 12px; }
  .letter-footer .affiliations li { width: 32px; height: 32px; }
</style>
</head>
<body>

<section class="card card-front" aria-label="Business card front">
  <svg class="wave" width="368" height="210" viewBox="0 0 368 210" aria-hidden="true">
    <path fill="var(--navy)" d="M0 0H368V80C300 92 230 72 170 46C130 28 100 18 80 18C45 18 15 35 0 55Z"/>
    <path fill="var(--sky)" d="M0 68C25 40 70 28 110 32C135 35 150 42 165 49C130 40 95 40 70 48C40 58 15 75 0 95Z"/>
  </svg>
  <div class="holder">
    <div class="holder-name">DANIEL HARLOW</div>
    <div class="holder-role">President</div>
  </div>
  <div class="brand-name">The Brightwater Joint Centre</div>
  <ul class="affiliations">
    <li role="img" aria-label="Crestmoor Lindell College of Surgeons badge"></li>
    <li role="img" aria-label="Varenwood Bone Health Association badge"></li>
  </ul>
  <ul class="contact-list">
    <li><svg viewBox="0 0 10 10"><path d="M2 0L4 2.5 3 4C3.8 5.6 4.6 6.4 6 7L7.5 6 10 8 8.5 10C4 9.5.5 6 0 1.5Z"/></svg>555-014-2210</li>
    <li><svg viewBox="0 0 10 10"><path d="M2 0H8V10H2ZM3 1V8H7V1Z"/></svg>555-017-3398</li>
    <li><svg viewBox="0 0 10 10"><path d="M2 0H8V3H10V8H0V3H2ZM1 9H9V10H1Z"/></svg>555-019-4476</li>
    <li><svg viewBox="0 0 10 10"><path d="M0 2H10V8H0ZM1 3L5 6 9 3Z" fill-rule="evenodd"/></svg>name@brightwaterjoint.example</li>
  </ul>
  <div class="card-address">
    <div>412 Kestrel Row</div>
    <div>Brightwater, Coastal 20418</div>
    <div class="web">www.brightwaterjoint.example</div>
  </div>
</section>

<section class="card card-back" aria-label="Appointment card back">
  <h2 class="appt-title">Next Appointment</h2>
  <div class="appt-row appt-name"><span class="dots"></span>has an apppointment</div>
  <div class="appt-row appt-when">Date :<span class="dots" style="margin-left:6px"></span>Time :<span class="dots"></span><span class="ampm">AM/PM</span></div>
  <ul class="day-list">
    <li>Sun</li><li>Mon</li><li>Tue</li><li>Wed</li><li>Thu</li><li>Fri</li><li>Sat</li>
  </ul>
  <p class="appt-note">Please give me 24 hours notice if you are unable to keep your appointment or<br>a cancellation fee may be charged.</p>
</section>

<section class="letterhead" aria-label="Letterhead">
  <svg class="wave" width="527" height="140" viewBox="0 0 527 140" aria-hidden="true">
    <path fill="var(--navy)" d="M0 0H527V122C470 135 400 128 330 108C280 94 240 82 200 66C160 48 120 34 85 32C50 30 20 44 0 58Z"/>
    <path fill="var(--sky)" d="M0 72C30 52 70 46 110 48C150 52 185 64 210 78C170 66 130 62 95 68C55 74 25 88 0 102Z"/>
  </svg>
  <ul class="letter-contact">
    <li>412 Kestrel Row</li>
    <li class="gap">Brightwater, Coastal 20418</li>
    <li>555-014-2210 <svg viewBox="0 0 10 10"><path d="M2 0L4 2.5 3 4C3.8 5.6 4.6 6.4 6 7L7.5 6 10 8 8.5 10C4 9.5.5 6 0 1.5Z"/></svg></li>
    <li>555-017-3398 <svg viewBox="0 0 10 10"><path d="M2 0H8V10H2ZM3 1V8H7V1Z"/></svg></li>
    <li>555-019-4476 <svg viewBox="0 0 10 10"><path d="M2 0H8V3H10V8H0V3H2ZM1 9H9V10H1Z"/></svg></li>
    <li>daniel@brightwaterjoint.example <svg viewBox="0 0 10 10"><path d="M0 2H10V8H0ZM1 3L5 6 9 3Z" fill-rule="evenodd"/></svg></li>
    <li>www.brightwaterjoint.example <svg viewBox="0 0 10 10"><circle cx="5" cy="5" r="5"/></svg></li>
  </ul>
  <div class="brand-name">The Brightwater Joint Centre</div>

  <div class="letter-body">
    <p class="salutation">Dear Mr. Harlow,</p>
    <p>Lorem ipsum dolor sit amet, consectetur adipiscing elit. Donec orci purus, luctus vitae dignissim eu, iaculis sed purus. Vivamus faucibus, ipsum nec aliquet viverra, leo mauris condimentum ligula, sit amet sagittis enim ligula quis arcu. Nam egestas tortor id nisi porttitor mattis. In tortor ante, ultricies in suscipit a, tempus non massa. Vivamus et auctor mi. Fusce vel massa nulla. Phasellus nec eros mauris, et scelerisque orci.</p>
    <p>Donec malesuada orci vitae nulla accumsan porta a id massa. Quisque accumsan iaculis magna sit amet fringilla. Maecenas consequat, magna eget tincidunt semper, odio nibh rutrum mi, id feugiat ante nisi eu risus. Vestibulum nunc orci, rhoncus a placerat in, ultricies in mi. Cras mattis varius eros, vel fringilla nisi suscipit eget. Quisque scelerisque sagittis nulla at porttitor.</p>
    <p>Sed id augue vitae urna euismod commodo aliquet a quam. Pellentesque arcu velit, cursus et malesuada ut, consequat et diam. Nullam erat sem, rhoncus id ullamcorper vitae, rhoncus et arcu. In ultricies ultricies nulla, ut rutrum nisi iaculis at. Donec eu magna a metus ornare faucibus. Fusce aliquet faucibus ultricies. Morbi semper, est id tincidunt gravida, sem arcu adipiscing lacus, ac bibendum nulla leo eu purus. Quisque nec diam sed risus consectetur a accumsan quis quis nibh. Vestibulum id purus lorem.</p>
    <p>It is a long established fact that a reader will be distracted by the readable content of a page when looking at its layout. The point of using Lorem Ipsum is that it has a more-or-less normal distribution of letters, as opposed to using 'Content here, content here', making it look like readable English. Many desktop publishing packages</p>
    <p class="closing">Sincerely,</p>
    <div class="signature-space" role="img" aria-label="Space for handwritten signature"></div>
  </div>

  <footer class="letter-footer">
    <ul class="affiliations">
      <li role="img" aria-label="Crestmoor Lindell College of Surgeons badge"></li>
      <li role="img" aria-label="Varenwood Bone Health Association badge"></li>
    </ul>
  </footer>
</section>

</body>
</html>
```